Lone Star Wetland Flora Stewardship Guild

We need to design the home page of this new website. We would like a fun website design for provides as a resource for members and information for potential members.
Please design so that we can see a portion of background on each side on the website.
I just need the final design files psd no coding needed.
Attached is their logo (colors are not 100% set in stone either so can mess with those as I did in the quick mockup attached)
Attached is a pdf newsletter they send out, you can get a feel for them and what they are about. The design is crappy and we are here to fix that going forward and we are starting with the website.
Here are some quick example websites (design style is open)
- I attached a quick mockup i did just for a content visual but by all means do what you want.
- http://www.brightpathleaders.example/
- http://www.civicunityhub.example/
- http://preview.webskinvault.example/show.php?cat=layouts&host=skinbazaar&temp=novaline
- http://www.meadowkeep.example/
- http://www.urbangleaners.example/
- http://www.projectcozyknit.example/
here are some of the other chapters website (pretty bad!)
and here are some of the others:
- http://www.dwrvcs.example/
- http://kwfg.example/
- http://www.blvcg.example/
Content Items that need to be included:
1. Logo
2. Menu - home, about, members, resources, events, membership, contact
3. Become a member - button or action
4. social links - chatterloop, workweave, clipstream
5. banner - that needs to explain their purpose "Promoting environmental stewardship through operations, research, education and outreach" (or this can be worked into the design)
6. Upcoming event (s)
7. Advertisement - members can place an ad on the website, this can be a placeholder for now
8. newsletter signup
9. advertise with us - this link can be in the footer
30-60 years of age, succesfull (household budgets of 120K+ men and women that live in texas.
Education

```html
<!DOCTYPE html>
<html lang="en">
<head>
<meta charset="utf-8">
<title>Lone Star Wetland Flora Stewardship Guild</title>
<link rel="stylesheet" href="https://fonts.googleapis.com/css2?family=Open+Sans:wght@400;600;700;800&display=swap">
<style>
:root{
  --maroon:#7d2543;
  --maroon-deep:#5b1a2d;
  --maroon-dark:#4a1424;
  --navy:#0d2158;
  --peach:#fde3b6;
  --peach-light:#fff3dc;
  --cream:#f6dcaa;
  --orange:#f2a43a;
  --ink:#1d1d1d;
  --rule:#8a8a8a;
  --field:#ececec;
}
*{box-sizing:border-box;margin:0;padding:0}
html,body{width:1200px;height:2196px;overflow:hidden}
body{position:relative;background:#fff;font-family:"Open Sans",Arial,sans-serif;color:var(--ink)}
.abs{position:absolute}

/* top bar */
.topbar{left:0;top:0;width:1200px;height:36px;background:linear-gradient(var(--maroon),var(--maroon-dark))}
.topbar .invite{left:752px;top:9px;font-size:12px;color:#fff}
.btn-top{top:5px;height:26px;border-radius:4px;font-size:12px;font-weight:600;line-height:26px;text-align:center}
.btn-signup{left:880px;width:72px;background:var(--navy);color:#fff}
.btn-login{left:962px;width:72px;background:var(--peach);color:var(--ink)}

/* header */
.header{left:0;top:36px;width:1200px;height:104px;background:linear-gradient(var(--peach-light),var(--peach))}
.brand{left:110px;top:22px;display:flex;align-items:center;gap:14px}
.brand-mark{width:52px;height:52px;background:var(--navy)}
.brand-name{font-size:21px;font-weight:700;line-height:25px;color:var(--ink);text-transform:uppercase}

/* nav */
.nav{left:0;top:140px;width:1200px;height:54px;background:linear-gradient(var(--maroon),var(--maroon-dark))}
.nav a{position:absolute;top:0;height:54px;line-height:54px;font-size:15px;color:#fff;text-decoration:none}
.nav a.active{border-top:3px solid #fff;line-height:48px}
.search{left:870px;top:13px;width:224px;height:30px;background:var(--peach);border-radius:3px;font-size:13px;color:#c8b590;padding:6px 12px}

/* hero */
.hero{left:0;top:194px;width:1200px;height:686px;background:linear-gradient(180deg,#bfe0f7 0%,#e8f3fb 22%,#5e8a4a 30%,#4a6a5e 42%,#6c8c88 60%,#7aa060 80%,#b46a3e 100%)}
.hero-title{left:0;top:100px;width:1200px;text-align:center;font-size:70px;line-height:82px;font-weight:800;color:var(--maroon);letter-spacing:1px;text-shadow:0 0 6px #fff,0 0 12px #fff}
.pillar{top:430px;display:flex;gap:12px;align-items:flex-start}
.pillar-bar{width:126px;height:12px;background:var(--navy);margin-top:8px;border:2px solid #fff}
.pillar-label{font-size:19px;font-weight:700;line-height:22px;color:#111;text-shadow:0 0 4px #fff}
.dots{top:616px;height:16px;border-radius:8px;border:2px solid #fff}

/* newsletter */
.newsletter{left:0;top:880px;width:1200px;height:142px;background:linear-gradient(var(--maroon),var(--maroon-dark))}
.newsletter h2{position:absolute;left:110px;top:12px;font-size:25px;font-weight:400;color:#fff}
.newsletter h2 span{color:var(--orange)}
.field{height:50px;background:var(--field);border-radius:5px;font-size:16px;color:#aaa;padding:13px 14px}
.btn-subscribe{left:878px;top:66px;width:214px;height:48px;background:var(--navy);color:#fff;font-size:19px;line-height:48px;text-align:center;border-radius:3px}

/* about */
.about{left:110px;top:1044px;width:636px;height:384px;background:var(--maroon-deep)}
.about h3{height:54px;background:var(--maroon);color:#fff;font-size:22px;font-weight:700;padding:12px 24px}
.about-photo{width:636px;height:178px;background:linear-gradient(180deg,#8fb06a,#4d7a44 45%,#2f5a3a 70%,#6d9a4c)}
.about p{padding:14px 22px 0;font-size:13px;line-height:20px;color:#fff}
.readmore{right:22px;bottom:14px;font-size:13px;color:#fff;text-decoration:underline}

/* events */
.events-head{left:766px;top:1052px;display:flex;align-items:center;gap:16px}
.events-head h3{font-size:23px;font-weight:800;color:var(--maroon)}
.event{left:764px;width:330px;height:88px;border-bottom:2px solid var(--rule)}
.event-thumb{left:0;top:18px;width:66px;height:46px}
.event-info{left:94px;top:10px;font-size:14px;line-height:18px;text-transform:uppercase}
.event-info .name{color:var(--maroon)}

/* ad and scene */
.scene{left:0;top:1490px;width:1200px;height:274px;background:linear-gradient(180deg,#ffffff 0%,#f1f4ee 45%,#c9cfc9 70%,#6e9c3a 88%,#3f7a22 100%)}
.ad{left:110px;top:1454px;width:984px;height:230px;background:var(--maroon-deep);color:var(--cream);font-size:35px;text-align:center;line-height:230px;text-transform:uppercase}
.scene-edge{left:0;top:1760px;width:1200px;height:4px;background:#c9b33a}

/* footer */
.footer{left:0;top:1764px;width:1200px;height:376px;background:var(--maroon-deep)}
.footer h4{position:absolute;top:24px;font-size:21px;font-weight:700;color:#fff}
.ad-links{left:110px;top:92px;list-style:none}
.ad-links li{font-size:11px;line-height:29px;color:#fff;padding-left:16px;position:relative}
.ad-links li::before{content:"";position:absolute;left:0;top:13px;width:4px;height:4px;background:#fff}
.input{left:392px;width:304px;background:#fff;font-size:12px;color:#aaa;padding:7px 10px}
.btn-send{left:392px;top:304px;width:82px;height:30px;background:var(--navy);color:#fff;font-size:12px;font-weight:600;line-height:30px;text-align:center}
.social{left:820px;display:flex;align-items:center;gap:28px;font-size:19px;color:var(--cream)}
.social i{display:block;width:14px;height:14px;background:#fff;border-radius:50%}

.copyright{left:0;top:2140px;width:1200px;height:56px;background:var(--navy);color:#fff;font-size:14px;padding:17px 110px}
</style>
</head>
<body>

<div class="abs topbar">
  <span class="abs invite">Become a member</span>
  <span class="abs btn-top btn-signup">SIGN UP</span>
  <span class="abs btn-top btn-login">LOGIN</span>
</div>

<header class="abs header">
  <div class="abs brand">
    <span class="brand-mark"></span>
    <span class="brand-name">Lone Star Wetland Flora<br>Stewardship Guild</span>
  </div>
</header>

<nav class="abs nav">
  <a class="active" style="left:122px">HOME</a>
  <a style="left:196px">ABOUT US</a>
  <a style="left:292px">MEMBERS</a>
  <a style="left:388px">RESOURCES</a>
  <a style="left:494px">EVENTS</a>
  <a style="left:574px">MEMBERSHIP</a>
  <a style="left:690px">CONTACT</a>
  <span class="abs search">Search</span>
</nav>

<section class="abs hero" role="img" aria-label="Photo of a pond covered with lily pads under a blue sky with trees on the far shore">
  <h1 class="abs hero-title">PROMOTING<br>ENVIRONMENTAL<br>STEWARDSHIP<br>THROUGH</h1>
  <div class="abs pillar" style="left:300px"><span class="pillar-bar"></span><span class="pillar-label">OPERATIONS<br>RESEARCH</span></div>
  <div class="abs pillar" style="left:606px"><span class="pillar-bar"></span><span class="pillar-label">EDUCATION AND<br>OUTREACH</span></div>
  <span class="abs dots" style="left:456px;width:92px;background:var(--navy)"></span>
  <span class="abs dots" style="left:556px;width:92px;background:var(--navy)"></span>
  <span class="abs dots" style="left:656px;width:92px;background:var(--maroon)"></span>
</section>

<section class="abs newsletter">
  <h2>Subscribe our <span>Newsletter</span>.</h2>
  <div class="abs field" style="left:110px;top:66px;width:354px">Name</div>
  <div class="abs field" style="left:490px;top:66px;width:352px">Email</div>
  <div class="abs btn-subscribe">SUBSCRIBE</div>
</section>

<section class="abs about">
  <h3>ABOUT LSWG</h3>
  <div class="about-photo" role="img" aria-label="Photo of lily pads and reeds with a white water lily"></div>
  <p>The Lone Star Wetland Flora Stewardship Guild, Inc. is an organization of scientists, educators, students, commercial pesticide applicators, administrators, and concerned individuals interested in the management and study of aquatic plants. The membership reflects a diversity of federal, state, and local agencies; universities and colleges around the world; corporations; and small businesses.</p>
  <a class="abs readmore">Read More</a>
</section>

<div class="abs events-head">
  <svg width="40" height="40" viewBox="0 0 40 40" aria-hidden="true">
    <rect x="3" y="7" width="34" height="30" rx="3" fill="none" stroke="#7d2543" stroke-width="3"/>
    <rect x="3" y="7" width="34" height="8" fill="#7d2543"/>
    <rect x="10" y="2" width="4" height="9" fill="#7d2543"/>
    <rect x="26" y="2" width="4" height="9" fill="#7d2543"/>
    <path d="M20 18l2.4 5 5.4.6-4 3.7 1.1 5.3-4.9-2.8-4.9 2.8 1.1-5.3-4-3.7 5.4-.6z" fill="#7d2543"/>
  </svg>
  <h3>UPCOMMING EVENTS</h3>
</div>

<div class="abs event" style="top:1108px">
  <div class="abs event-thumb" role="img" aria-label="Cedar Bend Lodge sign" style="background:#d8d8d8"></div>
  <div class="abs event-info"><div class="name">2014 LSWG Conference</div><div>January 22-24</div><div>Cedar Bend Ranch</div></div>
</div>
<div class="abs event" style="top:1196px">
  <div class="abs event-thumb" role="img" aria-label="Photo of a pond with lily pads" style="background:linear-gradient(#7ea05a,#b86a3c)"></div>
  <div class="abs event-info"><div class="name">2014 LSWG Conference</div><div>December 18-20</div><div>Cedar Bend Ranch</div></div>
</div>
<div class="abs event" style="top:1288px">
  <div class="abs event-thumb" role="img" aria-label="Photo of a pond surrounded by trees" style="background:linear-gradient(#a8c6a0,#3f6e3a)"></div>
  <div class="abs event-info"><div class="name">2014 LSWG Conference</div><div>October 12-14</div><div>Cedar Bend Ranch</div></div>
</div>
<div class="abs event" style="top:1376px">
  <div class="abs event-thumb" role="img" aria-label="Photo of a pond surrounded by trees" style="background:linear-gradient(#a8c6a0,#3f6e3a)"></div>
  <div class="abs event-info"><div class="name">2014 LSWG Conference</div><div>October 12-14</div><div>Cedar Bend Ranch</div></div>
</div>

<div class="abs scene" role="img" aria-label="Illustrated landscape of trees, faint houses and green grass"></div>
<div class="abs scene-edge"></div>
<div class="abs ad">Place your advertisment here!</div>

<footer class="abs footer">
  <h4 style="left:110px">ADVERTISE WITH US</h4>
  <ul class="abs ad-links">
    <li>Lorem ipsum dolor sit</li>
    <li>Amet consectetur</li>
    <li>Praesent vel sem id</li>
    <li>Curabitur hendrerit est</li>
    <li>Aliquam eget erat nec sapien</li>
    <li>Cras id augue nunc</li>
    <li>In nec justo non</li>
    <li>Vivamus mollis enim ut</li>
    <li>Curabitur hendrerit est</li>
  </ul>

  <h4 style="left:392px">Quick Message</h4>
  <div class="abs input" style="top:86px;height:32px">Name</div>
  <div class="abs input" style="top:128px;height:32px">Email</div>
  <div class="abs input" style="top:168px;height:128px">Messages</div>
  <div class="abs btn-send">SUBMIT</div>

  <h4 style="left:820px">Social Links</h4>
  <div class="abs social" style="top:90px"><i></i>Chatterloop</div>
  <div class="abs social" style="top:130px"><i></i>Chirpline</div>
  <div class="abs social" style="top:172px"><i></i>Workweave</div>
</footer>

<div class="abs copyright">© &nbsp;LSWG 2014. All Right Reserved</div>

</body>
</html>
```